Australian Trucking Company Requires Professional Looking Stationary

We require a professional looking stationary design that incorporates our newly designed logo.

Our business, called "Brell Haulage Contracting", provides contracting work, transport and logistics to business in Western Australia particularly with links to the mining sector.

We are a small business looking to expand and our new logo and our new stationary will help develop our brand image in our market place.

Target Market(s)

Businesses and Corporation with links to the Mining Sector

Industry/Entity Type

Small Business

Requirements
Must have
• The letterhead must have the following details:
The new logo

Text saying: "Brell Holdings Pty Ltd (ACN 582 316 907) ATF The Brell Discretionary Trust T/AS"
"ABN 71 834 209 553"
Address "P.O Box 817 Wattlegrove WA, 6958"
Phone: 08 9352 7140
Email: brellhaul@mailbox-example.com.au

The text on the letterhead should be editable as the details are likely to change in the near future. Provision should be made for a website address all though one isn't available at the moment.

The styling, layout and font text is entirely up to the designer.

```html
<!DOCTYPE html>
<html lang="en">
<head>
<meta charset="utf-8">
<title>Brell Haulage Contracting – Business Card</title>
<link rel="stylesheet" href="https://fonts.googleapis.com/css2?family=Open+Sans:wght@400;600;700;800&display=swap">
<style>
  :root {
    --stage: #6a4a33;
    --paper-top: #ffffff;
    --paper-bottom: #d9d9d9;
    --brand-red: #c4161c;
    --deep-red: #8a0a10;
    --bright-red: #e0222a;
    --ink-grey: #4a4a4a;
    --white: #ffffff;
  }
  * { box-sizing: border-box; margin: 0; padding: 0; }
  html, body {
    width: 1200px; height: 426px; overflow: hidden;
    background: var(--stage);
    font-family: "Open Sans", Arial, sans-serif;
  }
  .sheet { position: relative; width: 1200px; height: 426px; }
  .card {
    position: absolute; width: 519px; height: 295px;
    border-radius: 20px; overflow: hidden;
  }
  .card--front {
    left: 53px; top: 70px;
    background: linear-gradient(180deg, var(--paper-top) 0%, var(--paper-bottom) 100%);
  }
  .card--back {
    left: 606px; top: 68px;
    background: radial-gradient(ellipse 70% 80% at 45% 45%, var(--bright-red) 0%, #b5121a 45%, var(--deep-red) 100%);
  }
  .wave { position: absolute; left: 0; top: 0; width: 519px; height: 295px; }

  .brand {
    position: absolute; left: 26px; top: 36px;
    display: flex; align-items: center; gap: 12px;
  }
  .brand__mark { width: 16px; height: 16px; background: var(--brand-red); }
  .brand__name {
    color: var(--brand-red); font-weight: 800; font-size: 25px;
    line-height: 27px; text-transform: uppercase; letter-spacing: 0.5px;
  }

  .entity {
    position: absolute; left: 0; top: 160px; width: 222px;
    text-align: center; color: var(--ink-grey);
    font-size: 11.5px; line-height: 17px;
  }
  .entity__abn { margin-top: 2px; }

  .contact {
    position: absolute; right: 16px; top: 188px;
    text-align: right; color: var(--white);
  }
  .contact__name { font-size: 16px; font-weight: 700; line-height: 20px; }
  .contact__role { font-size: 11px; line-height: 14px; margin-bottom: 12px; }
  .contact__line {
    display: flex; justify-content: flex-end; align-items: center;
    gap: 4px; font-size: 11px; line-height: 18px; white-space: nowrap;
  }
  .contact__line svg { width: 9px; height: 9px; fill: var(--white); flex: none; }
  .contact__gap { width: 8px; }

  .back-name {
    position: absolute; left: 0; top: 0; width: 519px; height: 295px;
    display: flex; align-items: center; justify-content: center;
    color: var(--white); font-weight: 800; font-size: 34px;
    text-transform: uppercase; text-align: center; line-height: 40px;
    letter-spacing: 1px;
  }
</style>
</head>
<body>
<main class="sheet">
  <section class="card card--front" aria-label="Business card front">
    <svg class="wave" viewBox="0 0 519 295" aria-hidden="true">
      <defs>
        <linearGradient id="waveFill" x1="0" y1="0" x2="1" y2="1">
          <stop offset="0" stop-color="#d71d24"/>
          <stop offset="1" stop-color="#8a0a10"/>
        </linearGradient>
      </defs>
      <path d="M0,226 C120,260 260,172 519,100 L519,118 C260,190 120,282 0,250 Z" fill="#c9c9c9" opacity="0.6"/>
      <path d="M0,230 C120,264 260,176 519,104 L519,113 C260,185 120,274 0,240 Z" fill="#d9252c"/>
      <path d="M0,256 C130,300 270,196 519,128 L519,295 L0,295 Z" fill="url(#waveFill)"/>
      <path d="M0,256 C130,300 270,196 519,128 L519,136 C270,204 130,308 0,266 Z" fill="#b0141a"/>
    </svg>

    <div class="brand">
      <span class="brand__mark"></span>
      <div class="brand__name">Brell<br>Haulage<br>Contracting</div>
    </div>

    <div class="entity">
      <p>Brell Holdings Pty Ltd (ACN 582 316 907)</p>
      <p>ATF The Brell Discretionary Trust T/AS</p>
      <p class="entity__abn">ABN 71 834 209 553</p>
    </div>

    <div class="contact">
      <p class="contact__name">Persons name</p>
      <p class="contact__role">Manager</p>
      <p class="contact__line">
        <svg viewBox="0 0 10 10"><path d="M5,0 L10,5 L8.5,5 L8.5,10 L6,10 L6,7 L4,7 L4,10 L1.5,10 L1.5,5 L0,5 Z"/></svg>
        <span>P.O Box 817 Wattlegrove WA, 6958</span>
      </p>
      <p class="contact__line">
        <svg viewBox="0 0 10 10"><path d="M2,0 L4,2.5 L3,4 C4,6 5,7 6,7.5 L7.5,6.5 L10,8.5 L8.5,10 C4,9.5 0.5,6 0,1.5 Z"/></svg>
        <span>08 9352 7140</span>
        <span class="contact__gap"></span>
        <svg viewBox="0 0 10 10"><path d="M0,2 L10,2 L10,8 L0,8 Z M0.8,2.6 L5,5.6 L9.2,2.6 Z" fill-rule="evenodd"/></svg>
        <span>brellhaul@mailbox-example.com.au</span>
      </p>
    </div>
  </section>

  <section class="card card--back" aria-label="Business card back">
    <div class="back-name">Brell Haulage<br>Contracting</div>
  </section>
</main>
</body>
</html>
```